Harbor Law Stationary - Law Firm

I am looking for a designer who can help me design letterhead and envelopes consistent with our new business cards. Feel free to reach out to me directly at ned@harborlawgroup.example. Thank you!! Visit harborlawgroup.example to see our site and the attached files for creative assets.

Target Market(s)

Anyone needing a lawyer

Font styles to use
Other font styles liked:
• Adobe Caslon Pro

Requirements
Must have
• Adobe Caslon Pro font
Full color
Nice to have
• My photo on front along with 2/3 face of camo - see mock up for example of what I have in mind.

American colors - similar to the ones found on my website and gold.

```html
<!DOCTYPE html>
<html lang="en">
<head>
<meta charset="utf-8">
<title>Harbor Law Letterhead</title>
<link rel="stylesheet" href="https://fonts.googleapis.com/css2?family=EB+Garamond:wght@400&family=Open+Sans:wght@400&display=swap">
<style>
  :root {
    --backdrop: #dcdcdc;
    --paper: #f8f8f8;
    --gold: #a88f4a;
    --ink: #555555;
    --ink-dark: #3a3a3a;
    --navy: #0c2444;
    --white: #ffffff;
  }
  html, body {
    margin: 0;
    padding: 0;
    width: 1153px;
    height: 1200px;
    overflow: hidden;
    background: var(--backdrop);
  }
  .letterhead {
    position: absolute;
    left: 168px;
    top: 30px;
    width: 817px;
    height: 1140px;
    background: var(--paper);
    box-shadow: 0 10px 30px rgba(0,0,0,0.12);
    overflow: hidden;
  }
  .brand {
    position: absolute;
    left: 74px;
    top: 160px;
    width: 200px;
  }
  .brand-name {
    font-family: "EB Garamond", serif;
    font-weight: 400;
    font-size: 27px;
    color: var(--gold);
    line-height: 1;
    margin: 0;
  }
  .brand-tagline {
    font-family: "EB Garamond", serif;
    font-weight: 400;
    font-size: 10px;
    color: var(--ink-dark);
    margin: 5px 0 0;
    white-space: nowrap;
  }
  .contact {
    position: absolute;
    left: 592px;
    top: 89px;
    font-family: "EB Garamond", serif;
    font-size: 15px;
    line-height: 19px;
    color: var(--ink);
    font-style: normal;
    white-space: nowrap;
  }
  .contact span { display: block; }
  .contact .phone { margin-top: 4px; }
  .contact .email,
  .contact .web { line-height: 17px; }
  .letter-body {
    position: absolute;
    left: 74px;
    top: 286px;
    width: 669px;
    font-family: "Open Sans", sans-serif;
    font-size: 14.6px;
    line-height: 22px;
    color: var(--ink);
  }
  .letter-body p {
    margin: 0 0 22px;
    text-align: justify;
  }
  .signature {
    position: absolute;
    left: 74px;
    top: 863px;
    width: 95px;
    height: 89px;
    background: linear-gradient(135deg, rgba(30,30,30,0.08), rgba(30,30,30,0.02));
  }
  .services {
    position: absolute;
    left: 0;
    bottom: 0;
    width: 100%;
    height: 46px;
    background: var(--navy);
    display: flex;
    justify-content: center;
    align-items: center;
    gap: 12px;
    font-family: "EB Garamond", serif;
    font-size: 18px;
    color: var(--white);
    margin: 0;
    padding: 0;
    list-style: none;
  }
  .services li::before {
    content: "";
    display: inline-block;
    width: 6px;
    height: 6px;
    border-radius: 50%;
    background: var(--white);
    margin-right: 6px;
    vertical-align: middle;
  }
</style>
</head>
<body>
  <main class="letterhead">
    <header class="brand">
      <h1 class="brand-name">Harbor Law</h1>
      <p class="brand-tagline">Steady Counsel and Strong Advocacy Always</p>
    </header>

    <address class="contact">
      <span>48 Quayside Ave</span>
      <span>Bayport, FL 34000</span>
      <span class="phone">(555) 210-7384</span>
      <span class="email">mara@harborlawgroup.example</span>
      <span class="web">www.harborlawgroup.example</span>
    </address>

    <section class="letter-body">
      <p>Dear customer,</p>
      <p>Lorem ipsum dolor sit amet, consectetur adipisicing elit, sed do eiusmod tempor incididunt ut labore et dolore magna aliqua. Ut enim ad minim veniam, quis nostrud exercitation ullamco laboris nisi ut aliquip ex ea commodo consequat. Duis aute irure dolor in reprehenderit in voluptate velit esse cillum dolore eu fugiat nulla pariatur. Excepteur sint occaecat cupidatat non proident, sunt in culpa qui officia deserunt mollit anim id est laborum.</p>
      <p>Lorem ipsum dolor sit amet, consectetur adipisicing elit, sed do eiusmod tempor incididunt ut labore et dolore magna aliqua. Ut enim ad minim veniam, quis nostrud exercitation ullamco laboris nisi ut aliquip ex ea commodo consequat. Duis aute irure dolor in reprehenderit in voluptate velit esse cillum dolore eu fugiat nulla pariatur. Excepteur sint occaecat cupidatat non proident, sunt in culpa qui officia deserunt mollit anim id est laborum.</p>
      <p>Lorem ipsum dolor sit amet, consectetur adipisicing elit, sed do eiusmod tempor incididunt ut labore et dolore magna aliqua. Ut enim ad minim veniam, quis nostrud exercitation ullamco laboris nisi ut aliquip ex ea commodo consequat. Duis aute irure dolor in reprehenderit in voluptate velit esse cillum dolore eu fugiat nulla pariatur. Excepteur sint occaecat cupidatat non proident, sunt in culpa qui officia deserunt mollit anim id est laborum.</p>
      <p>Lorem ipsum dolor sit amet, consectetur adipisicing elit, sed do eiusmod tempor incididunt ut labore et dolore magna aliqua. Ut enim ad minim veniam, quis nostrud exercitation ullamco laboris nisi ut aliquip ex ea commodo consequat. Duis aute irure dolor in reprehenderit.</p>
      <p>Yours Sincerely,</p>
    </section>

    <div class="signature" role="img" aria-label="Handwritten signature"></div>

    <ul class="services">
      <li>Personal Injury</li>
      <li>Injunctions</li>
      <li>Criminal Defense</li>
      <li>Family Law</li>
    </ul>
  </main>
</body>
</html>
```